Website Design for Employee Moral and Happiness Company

Looking for a clean website design that explains our features in a step by step manner so our visitors know exactly what our site does before logging in.

The site is called "Velrato". See logo design and video for a sample of style and an overview of what we do.

Target Market(s)

Business owners that are looking to retain employees.

Number of Pages Required

1 page

```html
<!DOCTYPE html>
<html lang="en">
<head>
<meta charset="utf-8">
<title>Velrato — Employee Morale &amp; Happiness</title>
<link href="https://fonts.googleapis.com/css2?family=Jost:wght@400;500;600;700&family=Roboto+Slab:wght@400;600;700&family=Raleway:wght@400;500;600;700&display=swap" rel="stylesheet">
<style>
:root{
  --orange:#f26a21;
  --orange-light:#ff8a3d;
  --orange-deep:#f05322;
  --ink:#111111;
  --text:#555555;
  --muted:#8a8a8a;
  --soft:#f5f5f5;
  --line:#e3e3e3;
  --footer:#0d0d0d;
  --footer-bar:#232323;
  --white:#ffffff;
}
*{box-sizing:border-box;margin:0;padding:0}
html,body{width:1200px;height:4104px;overflow:hidden;background:var(--white)}
body{position:relative;font-family:"Raleway",sans-serif;color:var(--text)}
.abs{position:absolute}
a{color:inherit;text-decoration:none}

/* header */
.logo{position:absolute;font-family:"Roboto Slab",serif;font-weight:700;font-size:46px;letter-spacing:1px;color:var(--ink);line-height:1}
.site-logo{left:102px;top:14px}
.nav{position:absolute;top:30px;left:378px;display:flex;font-family:"Jost",sans-serif;font-size:15px;color:#333}
.nav a{position:absolute;white-space:nowrap}
.nav .active{color:var(--orange)}
.nav .active::after{content:"";position:absolute;left:0;right:0;top:26px;height:2px;background:var(--orange)}
.btn-contact{position:absolute;left:971px;top:22px;width:124px;height:37px;border-radius:20px;background:var(--white);color:var(--orange);font-family:"Jost",sans-serif;font-size:15px;display:flex;align-items:center;justify-content:center;z-index:3}

/* hero */
.hero-art{position:absolute;left:0;top:0;width:1200px;height:660px;z-index:1}
.hero-illustration{position:absolute;left:571px;top:151px;width:545px;height:375px;border-radius:14px;background:linear-gradient(135deg,#fde3d3,#f7b08a 60%,#e8e8e8);z-index:2}
.hero-copy{position:absolute;left:104px;top:225px;z-index:2;font-family:"Jost",sans-serif}
.hero-copy .lead{font-size:40px;color:var(--ink);line-height:1.2}
.hero-copy .accent{font-size:52px;font-weight:700;color:var(--orange);line-height:1.07}
.btn-dark{position:absolute;left:104px;top:417px;width:178px;height:47px;border-radius:24px;background:#2b2b2b;color:var(--white);font-family:"Jost",sans-serif;font-size:18px;display:flex;align-items:center;justify-content:center}

/* section headings */
.section-title{position:absolute;left:0;width:1200px;text-align:center;font-family:"Jost",sans-serif;font-size:46px;color:var(--ink);line-height:1}
.section-title span{color:var(--orange);font-weight:600}
.serif-title{font-family:"Roboto Slab",serif;font-weight:400}
.rule{position:absolute;height:3px;width:54px;background:var(--orange);left:573px}

.about-text{position:absolute;left:210px;top:768px;width:780px;text-align:center;font-size:16px;line-height:27px;color:#444}

/* feature cards */
.dots{position:absolute;left:88px;top:888px;width:160px;height:158px;background-image:radial-gradient(#c9c9c9 1.5px,transparent 1.6px);background-size:16px 16px}
.card{position:absolute;top:913px;width:312px;height:303px;background:var(--white);border-radius:70px 70px 0 70px;box-shadow:0 12px 30px rgba(0,0,0,.08);text-align:center;padding-top:44px}
.card.featured{background:linear-gradient(150deg,var(--orange-light),var(--orange-deep));border-radius:70px 0 0 70px;box-shadow:none}
.card .icon{width:76px;height:76px;border-radius:50%;background:var(--orange);margin:0 auto;display:flex;align-items:center;justify-content:center}
.card.featured .icon{background:var(--white)}
.card h3{font-family:"Jost",sans-serif;font-weight:600;font-size:17px;color:#222;line-height:21px;margin-top:22px}
.card.featured h3,.card.featured p{color:var(--white)}
.card p{font-size:13px;line-height:19px;color:#555;margin:14px auto 0;width:240px}

/* what we do */
.connector{position:absolute;left:0;top:0;width:1200px;height:4104px;z-index:0}
.illus{position:absolute}
.feature-title{position:absolute;font-family:"Jost",sans-serif;font-size:35px;color:var(--ink);line-height:37px}
.feature-title span{color:var(--orange)}
.feature-text{position:absolute;font-size:16px;line-height:28px;color:#555}
.btn-outline{position:absolute;border:2px solid var(--orange);border-radius:28px;color:var(--orange);font-family:"Jost",sans-serif;font-weight:600;font-size:15px;letter-spacing:.5px;display:flex;align-items:center;justify-content:center}

.orange-band{position:absolute;left:0;top:2027px;width:1200px;height:520px;z-index:1}
.band-title{position:absolute;left:123px;top:2160px;z-index:2;font-family:"Roboto Slab",serif;font-size:33px;line-height:37px;color:var(--white)}
.band-title b{font-weight:700}
.band-text{position:absolute;left:128px;top:2296px;width:410px;z-index:2;font-size:17.5px;line-height:26px;color:var(--white)}
.btn-white{position:absolute;left:124px;top:2399px;width:182px;height:48px;z-index:2;border:2px solid var(--white);border-radius:26px;color:var(--white);font-family:"Jost",sans-serif;font-weight:600;font-size:15px;letter-spacing:1px;display:flex;align-items:center;justify-content:center}

.soft-bg{position:absolute;left:0;top:2480px;width:1200px;height:672px;background:var(--soft);z-index:0}

/* contact */
.contact-title{position:absolute;left:0;width:1200px;text-align:center;font-family:"Roboto Slab",serif;font-size:39px;line-height:44px;color:var(--ink)}
.contact-title b{color:var(--orange);font-weight:600}
.field{position:absolute;border:1px solid #cfcfcf;border-radius:3px;font-size:13px;color:#555;padding:18px 0 0 20px;background:var(--white)}
.field.focus{background:#fdf0ea;border-color:#f4b79b}
.btn-submit{position:absolute;left:513px;top:3593px;width:153px;height:40px;border-radius:22px;background:linear-gradient(90deg,var(--orange-light),var(--orange-deep));color:var(--white);font-family:"Jost",sans-serif;font-size:16px;display:flex;align-items:center;justify-content:center}

/* footer */
.footer{position:absolute;left:0;top:3722px;width:1200px;height:314px;background:var(--footer)}
.footer .logo{color:var(--white);left:109px;top:76px}
.footer-about{position:absolute;left:112px;top:146px;width:240px;font-size:12.5px;line-height:19px;color:#bdbdbd}
.footer-col{position:absolute;top:82px}
.footer-col h4{font-family:"Jost",sans-serif;font-weight:500;font-size:21px;color:var(--white);line-height:1}
.footer-col h4::after{content:"";display:block;width:30px;height:2px;background:var(--orange);margin-top:6px}
.footer-col ul{list-style:none;margin-top:12px}
.footer-col li{font-size:13px;color:#e4e4e4;line-height:28px;padding-left:3px}
.socials{display:flex;gap:6px;margin-top:16px}
.socials span{width:26px;height:26px;border-radius:50%;background:var(--white)}
.socials span:first-child{background:var(--orange)}
.copy-bar{position:absolute;left:0;top:4036px;width:1200px;height:68px;background:var(--footer-bar);color:#9a9a9a;font-size:11.5px;text-align:center;line-height:68px}
</style>
</head>
<body>

<!-- hero backdrop -->
<svg class="hero-art" viewBox="0 0 1200 660" aria-hidden="true">
  <defs>
    <linearGradient id="heroGrad" x1="0" y1="0" x2="1" y2="1">
      <stop offset="0" stop-color="#ff8a3d"/>
      <stop offset="1" stop-color="#f05322"/>
    </linearGradient>
  </defs>
  <circle cx="1259" cy="-32" r="685" fill="url(#heroGrad)"/>
  <path d="M560 60 A700 700 0 0 0 990 640" fill="none" stroke="#f26a21" stroke-width="3"/>
</svg>

<div class="logo site-logo" style="z-index:3">Velrato</div>
<nav class="nav" style="z-index:3">
  <a class="active" style="left:0">About Us</a>
  <a style="left:116px">Our Services</a>
  <a style="left:260px">How it work</a>
  <a style="left:397px">Why Us</a>
  <a style="left:500px">Blogs</a>
</nav>
<a class="btn-contact">Contact Us</a>

<div class="hero-illustration" role="img" aria-label="Illustration of a team working together at a shared desk with laptops"></div>
<div class="hero-copy">
  <div class="lead">Velrato is here to</div>
  <div class="accent">help Businesses<br>like yours</div>
</div>
<a class="btn-dark" style="z-index:2">Get Started</a>

<!-- about -->
<h2 class="section-title" style="top:688px">About <span>Velrato</span></h2>
<div class="rule" style="top:739px;left:590px"></div>
<p class="about-text">Lorem Ipsum is simply dummy text of the printing and typesetting industry. Lorem Ipsum has been the industry's standard dummy text ever since the 1500s dummy text of the printingLorem Ipsum is simply dummy text of the printing and typesetting industry. Lorem Ipsum has been the industry's</p>

<div class="dots"></div>
<div class="card" style="left:115px">
  <div class="icon"><svg width="38" height="38" viewBox="0 0 38 38" fill="none" stroke="#fff" stroke-width="2"><circle cx="13" cy="19" r="6"/><circle cx="13" cy="19" r="2"/><rect x="23" y="8" width="9" height="7" rx="1"/><rect x="23" y="18" width="9" height="7" rx="1"/><rect x="23" y="28" width="9" height="5" rx="1"/></svg></div>
  <h3>Manage Your<br>Business</h3>
  <p>Lorem Ipsum is simply dummy text of the printing and typesetting industry. Lorem Ipsum has been</p>
</div>
<div class="card featured" style="left:448px">
  <div class="icon"><svg width="38" height="38" viewBox="0 0 38 38" fill="none" stroke="#f26a21" stroke-width="2"><rect x="7" y="7" width="24" height="25" rx="2"/><line x1="7" y1="13" x2="31" y2="13"/><path d="M11 17h4v4h-4zM17 17h4v4h-4zM23 17h4v4h-4zM11 23h4v4h-4zM17 23h4v4h-4z"/></svg></div>
  <h3>Event Manage<br>&amp; Planning</h3>
  <p>Lorem Ipsum is simply dummy text of the printing and typesetting industry. Lorem Ipsum has been</p>
</div>
<div class="card" style="left:792px">
  <div class="icon"><svg width="38" height="38" viewBox="0 0 38 38" fill="none" stroke="#fff" stroke-width="2"><path d="M7 31h25"/><path d="M10 30v-8M15 30v-11M20 30v-9M25 30v-14M30 30v-17"/><path d="M8 19l7-6 5 4 10-9"/><path d="M26 8h4v4"/></svg></div>
  <h3>Increase Employee<br>Retention</h3>
  <p>Lorem Ipsum is simply dummy text of the printing and typesetting industry. Lorem Ipsum has been</p>
</div>

<!-- what we do -->
<svg class="connector" viewBox="0 0 1200 4104" aria-hidden="true">
  <path d="M603 1404 V1440 Q603 1475 568 1475 H440 Q400 1475 400 1510" fill="none" stroke="#e6e6e6" stroke-width="8"/>
  <path d="M370 1900 V1950 Q370 1985 405 1985 H570 Q603 1985 603 2020 V2060" fill="none" stroke="#e6e6e6" stroke-width="8"/>
  <path d="M590 2540 V2590 Q590 2630 630 2630 H780 Q820 2630 820 2670 V2700" fill="none" stroke="#e0e0e0" stroke-width="8"/>
</svg>

<h2 class="section-title serif-title" style="top:1316px">What <span>We Do</span></h2>
<div class="rule" style="top:1370px;left:577px"></div>

<div class="illus" style="left:143px;top:1498px;width:391px;height:391px;border-radius:10px;background:linear-gradient(160deg,#f1f1f1,#fde1cf 55%,#eeeeee)" role="img" aria-label="Illustration of an employee working at a laptop at his desk"></div>
<h3 class="feature-title" style="left:633px;top:1544px">Increase Employee<br><span>Retention</span></h3>
<p class="feature-text" style="left:633px;top:1636px;width:480px">Lorem Ipsum is simply dummy text of the printing and typesetting industry. Lorem Ipsum has been the industry's standard dummy text ever since the 1500s, when an nknown.</p>
<p class="feature-text" style="left:633px;top:1738px;width:480px">printer took a galley of type and scrambled it to make a type specimen book. m Ipsum is simply dummy text</p>
<a class="btn-outline" style="left:633px;top:1823px;width:177px;height:50px">LEARN MORE</a>

<!-- orange band -->
<svg class="orange-band" viewBox="0 0 1200 520" preserveAspectRatio="none" aria-hidden="true">
  <defs>
    <linearGradient id="bandGrad" x1="0" y1="0" x2="1" y2="1">
      <stop offset="0" stop-color="#ff8a3d"/>
      <stop offset="1" stop-color="#f05322"/>
    </linearGradient>
  </defs>
  <path d="M0 0 H1200 V490 Q1100 460 940 485 Q760 520 560 505 Q300 480 140 470 Q50 465 0 505 Z" fill="url(#bandGrad)"/>
</svg>
<div class="soft-bg"></div>
<h3 class="band-title">Boost employee morale<br><b>and transform your<br>work events</b></h3>
<p class="band-text">Lorem Ipsum is simply dummy text of the printing and typesetting industry. Lorem Ipsum has been the industry's standard</p>
<a class="btn-white">LEARN MORE</a>
<div class="illus" style="left:550px;top:2128px;width:550px;height:351px;border-radius:12px;background:linear-gradient(160deg,#fbe7da,#ffffff 50%,#f6c6a6);z-index:2" role="img" aria-label="Illustration of a man holding a tablet beside a large analytics dashboard screen"></div>

<div class="illus" style="left:120px;top:2678px;width:430px;height:399px;border-radius:12px;background:linear-gradient(150deg,#ececec,#fde0cc 55%,#eaeaea);z-index:1" role="img" aria-label="Illustration of a person next to a large planning calendar with books and a pencil"></div>
<h3 class="feature-title" style="left:620px;top:2731px;z-index:1">From Raffles to <span>Auctions</span></h3>
<p class="feature-text" style="left:620px;top:2797px;width:495px;line-height:31px;z-index:1">Lorem Ipsum is simply dummy text of the printing and typesetting industry. Lorem Ipsum has been the industry's standard dummy text ever since the 1500s, whe an nknown. printer took a galley of type and scrambled it to make a type specimen book. m Ipsum is simply dummy text</p>
<a class="btn-outline" style="left:620px;top:2976px;width:196px;height:54px;font-weight:500;font-size:18px;letter-spacing:0;z-index:1">Learn More</a>

<!-- contact -->
<h2 class="contact-title" style="top:3224px">Start building your event<br><b>today with me!</b></h2>
<div class="rule" style="top:3323px;left:573px"></div>
<div class="field focus" style="left:288px;top:3351px;width:307px;height:45px">First Name</div>
<div class="field" style="left:606px;top:3351px;width:308px;height:45px">Last Name</div>
<div class="field" style="left:288px;top:3408px;width:307px;height:45px">Email address</div>
<div class="field" style="left:606px;top:3408px;width:308px;height:45px">Phone</div>
<div class="field" style="left:288px;top:3465px;width:625px;height:103px;padding-top:14px">Message</div>
<a class="btn-submit">Get Started</a>

<!-- footer -->
<footer class="footer">
  <div class="logo">Velrato</div>
  <p class="footer-about">Lorem Ipsum is simply dummy text of the printing and typesetting industry. Lorem Ipsum has been.</p>
  <div class="footer-col" style="left:462px">
    <h4>Navigation</h4>
    <ul><li>About Us</li><li>What We Do</li><li>Our Services</li><li>Why Us</li></ul>
  </div>
  <div class="footer-col" style="left:698px">
    <h4>Resources</h4>
    <ul><li>Support</li><li>Testimonials</li><li>FAQ</li><li>Contact Us</li></ul>
  </div>
  <div class="footer-col" style="left:921px">
    <h4>Stay in touch</h4>
    <div class="socials"><span></span><span></span><span></span><span></span></div>
  </div>
</footer>
<div class="copy-bar">© 2022 velrato. All rights reserved &nbsp;|&nbsp; Privacy &nbsp;|&nbsp;Terms of Use</div>

</body>
</html>
```